Website Design for my Copper Distillation Equipment Business Nature Sciencey Theme

I already have a website www.cascobrewworks.com and its a sitevelo website builder one. But I cannot get the design right at all. I need this fixed.

I have logo. I need a redesign, for my website, the home page, that maybe I can have something similar in design- I can use as template to copy, for other pages so the whole thing matches? Look at my website so you understand I have a few pages...but most are links. Its a competition. Code has to be easy for me to implement, I am not expert.

Your advice needed..It would be a plus if I can update this myself throughout time. If I could have this explained to me too, the maintenance of it...how would I do this too..etc..pretend I am a child when you explain, if you can. I am not good with this stuff but I am smart and can learn fast.

I want a high end look. Maybe like an ivy league college-y look too, real preppy, chemistry...science-y, nature like is good, leaves, drops water, fields of wheat, lavender, etc.

I want every page to look similar, but the home page is what I want to be the main showpiece,..and I want each page have a little text section, maybe a photos section and a video section, for that market. Like a nice website. If I am not doing this right, let me know. I can work with you. Just help me, please. Let me know if I am doing this right.

When I pick my winning design, for my website, I will hire the artist one-on-one to re-design my shopping cart next. Or if I need additional help with implementing this current design, I can hire the same artist again too. I have a blog that I may want to hire the redesign as well too, but later on. My point is I am not just looking for one project here but I want to follow up with winning artist. So it would be return business for the winner.

I got my logo done here so I am repeat customer. And I have given that winning artist other design work.

Target Market(s)

Moonshine Stills I sell most, Essential Oil Business, Micro and Craft Distilleries, Canna-businesses, Alcohol Fuel

Industry/Entity Type

Business

Number of Pages Required

5+ page

Colors
ec1f27

Requirements
Must have
• The categories for the stills must be prominent and eye catching. The main photo I would like to be naturelike theme, but you can try out different things with me. I am open to ideas and suggestions. I would like this to be implemented easy and fast.
Nice to have
• My logo in it. You can use any of my photos as well from my pictoshare account. https://www.pictoshare.com/photos/81724596@K09/
• Colors of my Logo...matching design.
• Maybe some basic stock photos you see would match for me..
• Chemistry like symbols for the categories, I love that.

```html
<!DOCTYPE html>
<html lang="en">
<head>
<meta charset="utf-8">
<title>Casco Brew Works – Copper Stills &amp; Distillation Equipment</title>
<link rel="stylesheet" href="https://fonts.googleapis.com/css2?family=Open+Sans:wght@400;600;700&family=Raleway:wght@400;500;600&display=swap">
<style>
:root{
  --gold-top:#f0ad12;
  --gold-bottom:#d98a00;
  --maroon-top:#5b1b20;
  --maroon-bottom:#2a0a0c;
  --btn:#3c0f13;
  --btn-top:#5a1a1f;
  --red-title:#a0151c;
  --ink:#222;
  --body:#555;
  --muted:#777;
  --white:#fff;
  --footer:#000;
}
*{margin:0;padding:0;box-sizing:border-box}
html,body{width:725px;height:1200px;overflow:hidden}
body{position:relative;background:var(--white);font-family:"Open Sans",sans-serif;color:var(--ink)}
h1,h2,h3,p{font-weight:400}
.abs{position:absolute}

/* Header */
.brand{left:0;width:725px;top:26px;display:flex;justify-content:center;align-items:center;gap:8px}
.brand-mark{width:14px;height:14px;background:var(--btn)}
.brand-name{font-family:"Raleway",sans-serif;font-weight:600;font-size:22px;color:var(--btn);letter-spacing:.5px}

.hero-band{left:0;top:109px;width:725px;height:120px;background:linear-gradient(#e9e9e9,#fff)}
.main-nav{left:115px;top:82px;width:495px;height:27px;background:linear-gradient(var(--gold-top),var(--gold-bottom));display:flex;border-radius:2px 2px 0 0}
.main-nav a{flex:auto;color:var(--white);text-decoration:none;font-size:8px;font-weight:700;display:flex;align-items:center;justify-content:center;border-right:1px solid rgba(0,0,0,.12)}
.main-nav a:last-child{border-right:0}

.hero{left:115px;top:109px;width:495px;height:213px;border-radius:0 0 4px 4px;background:linear-gradient(100deg,#6f7f5a 0%,#9aa78a 18%,#8a5a3a 38%,#3c3f4c 55%,#2a2a30 70%,#7d8f5c 100%)}
.hero-caption{left:214px;top:170px;width:304px;height:68px;background:rgba(20,20,20,.82);color:var(--white);text-align:center;font-family:"Raleway",sans-serif;padding-top:14px}
.hero-caption h1{font-weight:500;font-size:18px;letter-spacing:.3px;line-height:1.1}
.hero-caption p{font-size:11.5px;margin-top:2px;letter-spacing:.3px}
.hero-dots{left:340px;top:305px;display:flex;gap:3px}
.hero-dots span{width:9px;height:9px;border-radius:50%;background:var(--white)}

/* About */
.about-title{left:115px;top:355px;font-family:"Raleway",sans-serif;font-weight:400;font-size:17px}
.about-lead{left:115px;top:382px;width:285px;font-size:7px;line-height:11.5px;color:#333;font-weight:400}
.about-body{left:115px;top:410px;width:285px;font-size:5.3px;line-height:10px;color:var(--body)}
.btn{display:flex;align-items:center;justify-content:center;width:53px;height:15px;background:linear-gradient(var(--btn-top),var(--btn));color:var(--white);font-size:5.5px;font-weight:600;border-radius:2px;text-decoration:none}
.about-btn{left:115px;top:458px}
.video{left:414px;top:356px;width:196px;height:121px;border-radius:2px;background:linear-gradient(90deg,#6b3a22 0%,#8a5434 30%,#5b6f8c 60%,#4a6690 100%)}
.play{left:498px;top:403px;width:27px;height:27px}

/* Categories */
.categories{left:0;top:514px;width:725px;height:162px;background:linear-gradient(var(--maroon-top),var(--maroon-bottom))}
.cat-title{left:0;width:725px;top:537px;text-align:center;font-family:"Raleway",sans-serif;font-weight:400;font-size:12.5px;color:#c99a9c}
.cat-list{left:126px;top:578px;width:472px;display:flex;justify-content:space-between}
.cat{display:flex;flex-direction:column;align-items:center;width:58px}
.cat svg{width:32px;height:38px}
.cat span{color:var(--white);font-family:"Raleway",sans-serif;font-weight:400;font-size:8.5px;margin-top:5px;white-space:nowrap}
.cat-arrow{top:594px}

/* Cards */
.card-img{top:702px;width:157px;height:76px;border-radius:2px}
.card-title{top:786px;width:157px;font-family:"Raleway",sans-serif;font-weight:400;font-size:8.5px;line-height:14px;color:var(--red-title)}
.card-text{top:806px;width:157px;font-size:5.2px;line-height:10.3px;color:var(--body)}
.card-btn{top:882px}

/* Gallery */
.gallery-band{left:0;top:948px;width:725px;height:184px;background:linear-gradient(#e9e9e9,#fff 30%,#fff 75%,#ececec)}
.gallery-title{left:115px;top:998px;font-family:"Raleway",sans-serif;font-weight:400;font-size:16px}
.gallery-text{left:115px;top:1022px;width:250px;font-size:5.2px;line-height:9.5px;color:var(--body)}
.gallery-frame{left:402px;top:975px;width:190px;height:128px;background:var(--white);border:1px solid #ddd;padding:3px}
.gallery-photo{width:100%;height:100%;background:linear-gradient(90deg,#3f6a2c,#9a8a4e 40%,#b69b5a 55%,#5d7c8a 80%,#4f6e3a)}
.g-arrow{top:1023px;width:16px;height:28px;background:rgba(255,255,255,.85);display:flex;align-items:center;justify-content:center;font-size:13px;color:#222}

/* Footer */
.footer{left:0;top:1132px;width:725px;height:68px;background:var(--footer)}
.footer-nav{left:115px;top:1148px;font-size:7px;color:var(--white)}
.footer-nav span{margin:0 3px;color:var(--white)}
.footer-copy{left:115px;top:1164px;font-size:5.5px;color:#888}
.social{left:569px;top:1151px;display:flex;gap:3px}
.social span{width:11px;height:11px;background:var(--white);border-radius:2px}
</style>
</head>
<body>

<header>
  <div class="abs brand"><span class="brand-mark"></span><span class="brand-name">Casco Brew Works</span></div>
  <div class="abs hero-band"></div>
  <nav class="abs main-nav">
    <a href="#">HOME</a><a href="#">ABOUT US</a><a href="#">VIDEO</a><a href="#">PHOTOS</a><a href="#">BLOG</a><a href="#">LINKS</a><a href="#">SHOP</a><a href="#">BOOKS</a><a href="#">CONTACT</a>
  </nav>
  <div class="abs hero" role="img" aria-label="Close-up photo of a copper still with blue and red hoses outdoors"></div>
  <div class="abs hero-caption">
    <h1>FUSCE ULTRICIES ORCI FEUGIAT</h1>
    <p>ETIAM EST NUNC VENENATIS IN TRISTI</p>
  </div>
  <div class="abs hero-dots"><span></span><span></span><span></span><span></span></div>
</header>

<section>
  <h2 class="abs about-title">About Our Company &amp; Services</h2>
  <p class="abs about-lead">Class aptent taciti sociosqu ad litora torquent per conubia nostra per inceptos hymenaeos Proin nulla arcu nonummy luctus dictum eget fermentum et lorem .</p>
  <p class="abs about-body">Cras a ante vitae enim iaculis aliquam Mauris nunc quam venenatis nec euismod sit amet egestas placerat est Pellentesque habitant morbi tristique senectus et netus et malesuada fames ac turpis egestas Cras id elit Integer quis urna Ut ante enim dapibus malesuada fringilla eu condimentum quis tellusMorbi eget arcu Morbi porta libero id ullamcorper nonummy nibh ligula pulvinar metus eget</p>
  <a class="abs btn about-btn" href="#">READ MORE</a>
  <div class="abs video" role="img" aria-label="Video still of a man working on distillation equipment in a kitchen"></div>
  <svg class="abs play" viewBox="0 0 27 27"><circle cx="13.5" cy="13.5" r="13.5" fill="#fff"/><path d="M10.5 8 L19 13.5 L10.5 19Z" fill="#111"/></svg>
</section>

<section>
  <div class="abs categories"></div>
  <h2 class="abs cat-title">Please Choose the Category of the Still you are looking for</h2>
  <svg class="abs cat-arrow" style="left:106px" width="10" height="18" viewBox="0 0 10 18"><path d="M8 2 L2 9 L8 16" stroke="#fff" stroke-width="1.5" fill="none"/></svg>
  <svg class="abs cat-arrow" style="left:612px" width="10" height="18" viewBox="0 0 10 18"><path d="M2 2 L8 9 L2 16" stroke="#fff" stroke-width="1.5" fill="none"/></svg>
  <div class="abs cat-list">
    <div class="cat"><svg viewBox="0 0 30 36"><path d="M15 4 C15 4 6 18 6 23 a9 9 0 0 0 18 0 C24 18 15 4 15 4Z" fill="#fff"/></svg><span>Essential Oils</span></div>
    <div class="cat"><svg viewBox="0 0 30 36"><path d="M9 8 h6 l2-3 h4 v3 h1 a2 2 0 0 1 2 2 v20 a2 2 0 0 1-2 2 H9 a2 2 0 0 1-2-2 V10 a2 2 0 0 1 2-2Z" fill="#fff"/><path d="M15 16 c0 0-4 5-4 7 a4 4 0 0 0 8 0 c0-2-4-7-4-7Z" fill="#3a0f12"/></svg><span>Alchohol Fuel</span></div>
    <div class="cat"><svg viewBox="0 0 30 36"><g fill="#fff"><path d="M15 4 C17 10 17 18 15 24 C13 18 13 10 15 4Z"/><path d="M15 24 C11 18 6 15 3 14 C6 19 10 22 15 24Z"/><path d="M15 24 C19 18 24 15 27 14 C24 19 20 22 15 24Z"/><path d="M15 24 C11 22 6 22 4 23 C8 25 12 25 15 24Z"/><path d="M15 24 C19 22 24 22 26 23 C22 25 18 25 15 24Z"/><rect x="14.4" y="24" width="1.2" height="7"/></g></svg><span>Cannabis</span></div>
    <div class="cat"><svg viewBox="0 0 30 36"><rect x="12" y="3" width="6" height="4" fill="#fff"/><path d="M8 8 h14 l2 4 v14 l-2 4 H8 l-2-4 V12Z" fill="#fff"/><circle cx="15" cy="19" r="3.5" fill="#3a0f12"/></svg><span>Boliers</span></div>
    <div class="cat"><svg viewBox="0 0 30 36"><path d="M13 3 h4 v8 c2 2 3 4 3 7 v15 H10 V18 c0-3 1-5 3-7Z" fill="#fff"/></svg><span>Vodka Still</span></div>
    <div class="cat"><svg viewBox="0 0 30 36"><path d="M12 5 a3 3 0 0 1 6 0 v17 a6 6 0 1 1-6 0Z" fill="none" stroke="#fff" stroke-width="1.6"/><circle cx="15" cy="27" r="3" fill="#fff"/><path d="M15 12 v14" stroke="#fff" stroke-width="1.6"/><path d="M19 9h3M19 13h3M19 17h3" stroke="#fff" stroke-width="1"/></svg><span>Heat Control</span></div>
    <div class="cat"><svg viewBox="0 0 30 36"><path d="M22 8 a6 6 0 0 0-7 7 L6 24 l3 3 9-9 a6 6 0 0 0 7-7 l-3 3-3-1-1-3Z" fill="#fff"/></svg><span>Parts</span></div>
    <div class="cat"><svg viewBox="0 0 30 36"><path d="M13 4 h4 v5 c4 1 7 3 7 7 H6 c0-4 3-6 7-7Z" fill="none" stroke="#fff" stroke-width="1.5"/><path d="M4 28 L8 16 H22 L26 28Z" fill="none" stroke="#fff" stroke-width="1.5"/><path d="M17 6 h8 l3 4" stroke="#fff" stroke-width="1.5" fill="none"/><path d="M3 30 h24" stroke="#fff" stroke-width="1.5"/></svg><span>Distillery</span></div>
  </div>
</section>

<section>
  <div class="abs card-img" style="left:115px;background:linear-gradient(90deg,#6e6e6a,#9a938a 40%,#a58a6a 60%,#76726c)" role="img" aria-label="Photo of two copper pot stills against a brick wall"></div>
  <h3 class="abs card-title" style="left:115px">Home Distillers! We sell Copper Stills</h3>
  <p class="abs card-text" style="left:115px">If you can boil water, you can distill. We sell a small 2 inch diameter 15 gallon moonshine still called, the "Lanternfield". Handcrafted and individually numbered. Our commitment to fine craftsmanship can be seen in every detail in each piece. We can do custom designs for each client as well. Our Copper Reflux towers can also double as a Pot Still. See the Stills page for more info.</p>
  <a class="abs btn card-btn" style="left:115px" href="#">READ MORE</a>

  <div class="abs card-img" style="left:285px;background:linear-gradient(90deg,#5c6b8a,#b8b8b8 40%,#c23a2a 65%,#3a3a40)" role="img" aria-label="Photo of a micro distillery boiler with copper column"></div>
  <h3 class="abs card-title" style="left:285px">Micro Distillery Equipment- Copper Stills for Sale!</h3>
  <p class="abs card-text" style="left:285px;top:820px">We make Distillery Kits. We make 20 feet tall, 50 to100 Gallon Copper Stills, Pot Stills and Heat controls, Propane or Electric. Call me, if you have a distillery you want to set up or need another still. I sell stills to fit any ceiling, up to 6 inches in Diameter in Glass or Copper.</p>
  <a class="abs btn card-btn" style="left:285px" href="#">READ MORE</a>

  <div class="abs card-img" style="left:454px;background:linear-gradient(90deg,#4a4a3a,#8a9a5a 40%,#b6b87a 60%,#5a5a48)" role="img" aria-label="Photo of a glass funnel filtering green herbal oil into a jar"></div>
  <h3 class="abs card-title" style="left:454px">Meadow Herbal Extractor- Make Cannabis Oil with Alcohol!</h3>
  <p class="abs card-text" style="left:454px;top:815px">This Marijuana industry is going to be bigger than Alcohol and Tobacco- combined! So all you distilling professionals, look into this, for it is coming to a state near you. Its bigger also in tax receipts and profitability in privatized businesses. The butane industry (most cannabis oil made with), does NOT care about the health care</p>
  <a class="abs btn card-btn" style="left:454px" href="#">READ MORE</a>
</section>

<section>
  <div class="abs gallery-band"></div>
  <h2 class="abs gallery-title">Photo Gallery</h2>
  <p class="abs gallery-text">Curabitur iaculis tempus eros Curabitur vel mi sit amet magna malesuada ultrices Ut nisi erat fermentum vel congue id euismod in elit Fusce ultricies orci ac feugiat suscipit leo massa sodales velit et scelerisque mi tortor at ipsum cligula augue bibendum accumsan vestibulum<br>ut commodo a mi Morbi ornare gravida elit Integer congue augue et malesuada iaculis ipsum dui aliquet felis at cursus magna nisl nec elit Praesent elementum elit at</p>
  <div class="abs gallery-frame"><div class="gallery-photo" role="img" aria-label="Photo of a tall copper still in a garden beside a heat controller"></div></div>
  <div class="abs g-arrow" style="left:402px;border-radius:0 14px 14px 0">‹</div>
  <div class="abs g-arrow" style="left:576px;border-radius:14px 0 0 14px">›</div>
</section>

<footer>
  <div class="abs footer"></div>
  <div class="abs footer-nav">Home<span>|</span>About Us<span>|</span>VIDEO<span>|</span>PHOTOS<span>|</span>BLOG<span>|</span>LINKS<span>|</span>SHOP<span>|</span>BOOKS<span>|</span>CONTACT</div>
  <div class="abs footer-copy">© 2015 Company Name &nbsp;All right reserved &nbsp;Term of Use</div>
  <div class="abs social" aria-label="Social links"><span></span><span></span><span></span></div>
</footer>

</body>
</html>
```